I have a business that exists already (Linden Conservatory of Music) that we offer music lessons to all instruments. I recently opened a smaller version called CHORDS by Linden that will only teach piano lessons. What I'm looking for now is a 3 page Website on word press. After I choose the design I like I want to be able to take over the website and bring it to our hosting company. We want full control of it and our team will take over. The reason I'm doing this is to have other visions and ideas from others. The first page will be about the company and our message/vision. Second page about the piano lessons. The third will be about franchising this concept "Chords by Linden" Attached are 3 Logos . Please refer to our existing website www.lindenmusicconservatory.example to look at our piano page and franchising page. Please feel free to message me if you need more info. Thanks
Please note I do not want the new website (Chords by Linden) To look like the other Website (Linden Conservatory of Music) Fresh new look. I do not want the colours red or using the Red logo. I only provided it so that you have an Idea of What the other business looks like and that you can take the piano content and franchise content off of it. Chords by Linden is smaller concept and only piano lessons.
Thanks
Only Piano lessons for all students
3 page

```html
<!DOCTYPE html>
<html lang="en">
<head>
<meta charset="utf-8">
<title>Chords by Linden – Piano Lessons</title>
<link rel="stylesheet" href="https://fonts.googleapis.com/css2?family=Cinzel:wght@400;600&family=Gelasio:ital,wght@0,400;0,700;1,400&display=swap">
<style>
:root{
  --blue:#1f9bf2;
  --ink:#1d1d1d;
  --body:#333;
  --panel:#f2f2f2;
  --white:#fff;
}
*{margin:0;padding:0;box-sizing:border-box}
html,body{width:1200px;height:2783px;overflow:hidden;background:var(--white)}
body{position:relative;font-family:"Gelasio",Georgia,serif;color:var(--body)}
h2{font-weight:400}
.abs{position:absolute}
.btn{display:flex;align-items:center;justify-content:center;height:35px;background:var(--blue);color:var(--white);font-family:"Cinzel",Georgia,serif;font-size:17px;letter-spacing:.5px;flex:none}
.abs.btn{position:absolute}
.rule{position:absolute;height:2px;background:var(--blue);width:34px}

/* header */
.site-header{left:0;top:0;width:1200px;height:93px;background:var(--white)}
.brand{left:143px;top:24px;font-family:"Cinzel",Georgia,serif;font-size:34px;color:var(--ink);display:flex;align-items:center;gap:10px}
.brand .dot{width:14px;height:14px;background:var(--ink)}
.nav{right:141px;top:37px;display:flex;gap:36px;font-family:"Cinzel",Georgia,serif;font-size:14px;letter-spacing:1px;color:#333;text-transform:uppercase}
.nav .active{color:var(--blue)}

/* hero */
.hero{left:0;top:93px;width:1200px;height:480px;background:linear-gradient(90deg,#3a2f26 0%,#a58b6f 22%,#e9dcc9 45%,#f1e4cf 70%,#efe0c6 100%)}
.hero-copy{right:143px;top:225px;text-align:right;color:var(--ink);font-family:"Cinzel",Georgia,serif}
.hero-copy .l1{font-size:31px;line-height:40px}
.hero-copy .l2{font-size:47px;line-height:58px;font-weight:600}
.hero-copy .l3{font-size:31px;line-height:40px}

/* about */
.about-title{left:0;width:1200px;top:645px;text-align:center;font-family:"Cinzel",Georgia,serif;font-size:32px;color:var(--ink)}
.about-title small{font-size:16px}
.about-sub{left:0;width:1200px;top:708px;text-align:center;font-style:italic;font-size:22px;color:var(--ink)}
.about-body{left:155px;width:890px;top:746px;display:flex;flex-direction:column;align-items:center;text-align:center;font-size:14.5px;line-height:25.5px}
.about-body p+p{margin-top:8px}
.about-body .btn{margin-top:14px;width:155px}

/* vision */
.vision-photo{left:0;top:998px;width:595px;height:543px;background:linear-gradient(120deg,#d8d6d2 0%,#7b8797 40%,#e5e1da 70%,#f3f1ee 100%)}
.vision-panel{left:595px;top:998px;width:605px;height:543px;background:var(--panel)}
.bar{position:absolute;width:6px;background:var(--blue)}
.sec-title{font-family:"Cinzel",Georgia,serif;color:var(--ink)}
.vision-body{left:635px;top:1180px;width:430px;font-size:14.5px;line-height:25.5px;display:flex;flex-direction:column;align-items:flex-start}
.vision-body p+p{margin-top:5px}
.vision-body .btn{margin-top:12px;margin-left:2px;width:184px}

/* programs */
.programs-title{left:142px;top:1665px;font-size:25px;line-height:36px;color:var(--ink)}
.programs-body{left:142px;top:1766px;width:440px;display:flex;flex-direction:column;align-items:flex-start}
.programs-list{list-style:none;font-size:14.5px;line-height:25.5px}
.programs-list li{position:relative;padding-left:26px;margin-bottom:7px}
.programs-list svg{position:absolute;left:0;top:6px}
.programs-body .btn{margin-top:14px;width:183px}
.programs-photo{left:604px;top:1620px;width:596px;height:543px;background:linear-gradient(135deg,#2f2924 0%,#6b5645 40%,#b48c6a 65%,#3b3128 100%)}

/* franchise */
.fr-title{left:0;width:1200px;top:2237px;text-align:center;font-family:"Cinzel",Georgia,serif;font-size:38px;color:var(--ink)}
.fr-sub{left:0;width:1200px;top:2296px;text-align:center;font-size:17px;color:#333}

/* footer */
.footer{left:0;top:2437px;width:1200px;height:312px;background:linear-gradient(180deg,#3c4654 0%,#2a323c 60%,#1f262e 100%)}
.contact{position:absolute;top:2533px;width:260px;text-align:center;color:var(--white);font-size:14px;line-height:22px}
.contact .ring{width:70px;height:70px;border-radius:50%;background:var(--white);margin:0 auto 14px;display:flex;align-items:center;justify-content:center}
.contact .label{font-family:"Cinzel",Georgia,serif;font-size:15px;letter-spacing:1px}
.bottom{left:0;top:2749px;width:1200px;height:34px;background:var(--blue);color:var(--white);font-size:13px}
.bottom .copy{position:absolute;left:142px;top:9px}
.bottom .social{position:absolute;right:140px;top:11px;display:flex;gap:14px}
.bottom .social span{width:12px;height:12px;border-radius:50%;background:var(--white)}
</style>
</head>
<body>

<header class="abs site-header">
  <div class="abs brand"><span class="dot"></span>CHORDS by Linden</div>
  <nav class="abs nav"><span class="active">Home</span><span>Piano Lessons</span><span>Franchising</span><span>Contact Us</span></nav>
</header>

<section class="abs hero" role="img" aria-label="Girl smiling while playing an upright piano in a bright room"></section>
<div class="abs hero-copy">
  <div class="l1">We Will Provide</div>
  <div class="l2">PIANO LESSONS</div>
  <div class="l3">For All Students</div>
</div>
<a class="abs btn" style="left:875px;top:383px;width:184px">Contact Us Today</a>

<h2 class="abs about-title">ABOUT CHORDS <small>by Linden</small></h2>
<div class="rule" style="left:583px;top:690px"></div>
<div class="abs about-sub">Playing the Piano</div>
<div class="abs about-body">
  <p>When you think of a piano, you probably envision black and white keys but the piano is more than those harmonious sounds created by the player. The versatility and the musicianship instilled into the player&nbsp; from those keys is the true magic that comes from playing piano!</p>
  <p>Starting from the grassroots, experience different methods and styles of playing piano. To mark the milestones of progression, engage in one of Linden’s many unique performance opportunities like annual festival competitions, recitals or our examinations (Linden &amp; NMB). Penultimately, at the end of the journey, join our elite teaching program to bring the same joy of learning the piano to another student.</p>
  <a class="btn">Read More</a>
</div>

<div class="abs vision-photo" role="img" aria-label="Boy playing a white grand piano with his smiling teacher beside him"></div>
<div class="abs vision-panel"></div>
<div class="bar" style="left:596px;top:1093px;height:352px"></div>
<h2 class="abs sec-title" style="left:635px;top:1118px;font-size:32px">OUR VISION</h2>
<div class="rule" style="left:635px;top:1171px"></div>
<div class="abs vision-body">
  <p>Our Mission is Lorem ipsum dolor sit amet, consectetuer adipiscig elit, sed diama nonummy nibh euismod tincidunt ut laoreet dolore magna aliquam erat volutpat. Ut wisi enim ad minim veniam.</p>
  <p>Lorem hendrerit in vulputate velit esse molestie consequat, velocity illum dolore eu feugiat nulla facilisis at vero eros et accumsan etlict iusto odio dignissim qui blandit praesent luptatum zzril delenit loei augue duis dolore te feugait nulla facilisi.</p>
  <a class="btn">Contact Us Today</a>
</div>

<h2 class="abs programs-title">OUR PROGRAMS ALSO PROVIDE<br>STUDENTS THE OPPORTUNITY TO:</h2>
<div class="rule" style="left:143px;top:1751px"></div>
<div class="abs programs-body">
  <ul class="programs-list">
    <li><svg width="15" height="12" viewBox="0 0 15 12"><path d="M1 5h6l-2-4h3l5 4v5H4L1 8z" fill="none" stroke="#1f9bf2" stroke-width="1.3"/></svg>Participate in large-scale performances.</li>
    <li><svg width="15" height="12" viewBox="0 0 15 12"><path d="M1 5h6l-2-4h3l5 4v5H4L1 8z" fill="none" stroke="#1f9bf2" stroke-width="1.3"/></svg>Perform at Linden’s many community events on a regular basis.</li>
    <li><svg width="15" height="12" viewBox="0 0 15 12"><path d="M1 5h6l-2-4h3l5 4v5H4L1 8z" fill="none" stroke="#1f9bf2" stroke-width="1.3"/></svg>Access the GTA’s coolest Broadcast stage</li>
    <li><svg width="15" height="12" viewBox="0 0 15 12"><path d="M1 5h6l-2-4h3l5 4v5H4L1 8z" fill="none" stroke="#1f9bf2" stroke-width="1.3"/></svg>Attend Clinics, Masterclasses, and Jam Nights</li>
    <li><svg width="15" height="12" viewBox="0 0 15 12"><path d="M1 5h6l-2-4h3l5 4v5H4L1 8z" fill="none" stroke="#1f9bf2" stroke-width="1.3"/></svg>Access the Linden Rocks band program. Linden’s Band Program empowers and electrifies students to come together, create music and confidently hit the stage with their own band identity while having fun and honing their instrument.</li>
    <li><svg width="15" height="12" viewBox="0 0 15 12"><path d="M1 5h6l-2-4h3l5 4v5H4L1 8z" fill="none" stroke="#1f9bf2" stroke-width="1.3"/></svg>Register in our elite teaching program to learn how to pass on the magic and passion of playing the piano to students.</li>
  </ul>
  <a class="btn">Contact Us Today</a>
</div>
<div class="bar" style="left:597px;top:1715px;height:352px"></div>
<div class="abs programs-photo" role="img" aria-label="Young girl in a polka-dot top playing a digital piano in a group music class"></div>

<h2 class="abs fr-title">Franchise Opportunities</h2>
<div class="abs fr-sub">BE PART OF THE LINDEN CONSERVATORY FAMILY</div>
<a class="abs btn" style="left:529px;top:2332px;width:141px;font-size:15px">Know More</a>

<footer class="abs footer" role="img" aria-label="Dusky city waterfront skyline behind a dark overlay"></footer>
<div class="contact" style="left:183px">
  <div class="ring"><svg width="26" height="34" viewBox="0 0 26 34"><path d="M13 1C6.4 1 1 6.2 1 12.7 1 21 13 33 13 33s12-12 12-20.3C25 6.2 19.6 1 13 1z" fill="#1f9bf2"/><circle cx="13" cy="12.5" r="4.5" fill="#fff"/></svg></div>
  <div class="label">Chords by Linden</div>
  <div>123, Building Name, Street</div>
  <div>City, State XY 123456</div>
</div>
<div class="contact" style="left:477px">
  <div class="ring"><svg width="28" height="28" viewBox="0 0 28 28"><path d="M6 3l5 1 2 6-3 2c1.5 3.5 3.5 5.5 7 7l2-3 6 2 1 5c-1 2-3 3-5 3C11 26 2 17 2 7c0-2 2-4 4-4z" fill="#1f9bf2"/></svg></div>
  <div class="label">Call Us</div>
  <div>1-888-555-0142</div>
</div>
<div class="contact" style="left:759px">
  <div class="ring"><svg width="32" height="22" viewBox="0 0 32 22"><rect x="1" y="1" width="30" height="20" fill="#1f9bf2"/><path d="M1 1l15 11L31 1M1 21l11-10M31 21L20 11" fill="none" stroke="#fff" stroke-width="1.6"/></svg></div>
  <div class="label">Email Us</div>
  <div>inquiry@chordsbylinden.example</div>
</div>

<div class="abs bottom">
  <div class="copy">Copyright © 2020 <b>Chords By Linden</b>. All Rights Reserved.</div>
  <div class="social"><span></span><span></span><span></span><span></span></div>
</div>

</body>
</html>
```